Logistics Website Design

See website https://tqfreightglobal.com for theme and color details. Need the site to be re-done and reflect some of the designs shown in this list here: https://pixelvane.com/tags/logistics-company-website

Target Market(s)

Logistics & Transportation

Industry/Entity Type

Logistics and Supply Chain

Coding

Number of Pages Required

5+ page

Requirements
Must have
• Colors must match theme of logo. Looking for a sleek, interactive design.

```html
<!DOCTYPE html>
<html lang="en">
<head>
<meta charset="utf-8">
<title>TQ Freight Global — Home</title>
<link rel="stylesheet" href="https://fonts.googleapis.com/css2?family=Figtree:wght@400;500;600;700;800&family=Lato:wght@400;700&display=swap">
<style>
:root{
  --orange:#e0512a;
  --orange-deep:#c9421f;
  --black:#0b0b0b;
  --ink:#1a1a1a;
  --muted:#4a4a4a;
  --white:#ffffff;
  --panel:#f4f4f4;
}
*{box-sizing:border-box;margin:0;padding:0}
html,body{width:1200px;height:4219px;overflow:hidden;background:var(--white)}
body{font-family:"Lato",sans-serif;color:var(--ink)}
.page{position:relative;width:1200px;height:4219px;overflow:hidden}
.abs{position:absolute}
.heading{font-family:"Figtree",sans-serif;font-weight:800;text-transform:uppercase;letter-spacing:-.3px}
.eyebrow{font-family:"Figtree",sans-serif;font-weight:600;font-size:16px;color:var(--orange);text-transform:uppercase}
.rule{height:3px;width:98px;background:var(--orange)}
.btn{display:flex;align-items:center;justify-content:center;background:var(--orange);color:var(--white);font-family:"Figtree",sans-serif;font-weight:700;font-size:15px;border-radius:30px;text-transform:uppercase}

/* hero */
.hero-photo{left:0;top:0;width:1200px;height:700px;background:linear-gradient(180deg,#3a2a24 0%,#7a3a1c 22%,#b4521f 36%,#4a2e24 55%,#1e1d22 80%,#151518 100%)}
.brand{left:150px;top:11px;width:150px;height:150px;border-radius:50%;background:var(--black);border:4px solid var(--orange);display:flex;align-items:center;justify-content:center;text-align:center;color:var(--white);font-family:"Figtree",sans-serif;font-weight:800;font-size:19px;line-height:1.1}
.nav{left:298px;top:65px;width:750px;height:46px;border-radius:30px;background:var(--black);display:flex;align-items:center;padding-left:36px;font-family:"Figtree",sans-serif;font-weight:500;font-size:15px;color:var(--white);gap:30px}
.nav .active{color:var(--orange)}
.nav .caret{font-size:10px;margin-left:6px}
.nav .btn{margin-left:auto;margin-right:8px;width:164px;height:40px;text-transform:none;font-size:17px}
.hero-title{left:0;top:300px;width:1200px;text-align:center;color:var(--white);font-size:48px;line-height:1.1}
.hero-sub{left:0;top:424px;width:1200px;text-align:center;color:var(--white);font-family:"Figtree",sans-serif;font-weight:500;font-size:18px}
.hero .btn{left:504px;top:466px;width:190px;height:39px}

/* about */
.about-art{left:130px;top:752px;width:490px;height:444px;border-radius:50%;background:radial-gradient(circle at 50% 40%,#dfe9f7 0%,#8fb2dd 45%,#2f5fa6 70%,#ffffff 71%)}
.about-copy{left:670px;top:770px;width:380px}
.about-copy h2{font-size:38px;margin-top:16px}
.about-copy .rule{margin-top:10px}
.about-copy p{margin-top:24px;font-size:12.3px;line-height:22.5px;color:var(--muted);text-align:justify}
.about-copy .btn{margin-top:26px;width:146px;height:41px}

/* services */
.center{left:0;width:1200px;text-align:center}
.center .rule{margin:0 auto}
.section-title{font-size:38px;line-height:1.2}
.card{top:1486px;width:214px;height:348px;background:var(--black);border-radius:0 0 107px 107px;color:var(--white);text-align:center;padding:110px 28px 0}
.card.featured{background:var(--orange)}
.card h3{font-family:"Figtree",sans-serif;font-weight:600;font-size:17px;line-height:22px;text-transform:uppercase}
.card p{margin-top:14px;font-size:12px;line-height:18.5px}
.card-photo{top:1412px;width:158px;height:158px;border-radius:50%;border:3px solid var(--white)}

/* welcome */
.welcome-photo{left:0;top:1943px;width:1200px;height:660px;background:linear-gradient(95deg,#e0562a 0%,#dd5d31 32%,#c8694a 48%,#8f5a52 62%,#5c5a68 78%,#3f5160 100%)}
.welcome-copy{left:149px;top:2030px;width:443px;color:var(--white)}
.welcome-copy .eyebrow{color:var(--white)}
.welcome-copy h2{margin-top:14px;font-size:40px;line-height:53px}
.welcome-copy .rule{margin-top:14px;background:var(--white);width:80px}
.welcome-copy p{margin-top:30px;font-size:16px;line-height:30px;text-align:justify}

/* industries */
.industry{top:2862px;width:150px;text-align:center}
.industry .ring{width:94px;height:94px;margin:0 auto;border-radius:50%;border:2px solid var(--orange);background:var(--white);display:flex;align-items:center;justify-content:center}
.industry.featured .ring{background:var(--orange)}
.industry span{display:block;margin-top:22px;font-family:"Figtree",sans-serif;font-weight:700;font-size:13px;line-height:17px;text-transform:uppercase}
.dash{top:2890px}

/* contact */
.contact-card{left:149px;top:3118px;width:900px;height:627px;background:var(--panel);border-radius:24px}
.field{background:var(--white);border:1px solid #e2e2e2;border-radius:10px;box-shadow:0 3px 6px rgba(0,0,0,.1);font-size:11px;color:#555;padding:18px 16px}
.contact .btn{left:522px;top:3641px;width:154px;height:41px}

/* footer */
.footer-brand{left:158px;top:3832px;width:260px;height:260px;border-radius:50%;background:var(--black);border:6px solid var(--orange);display:flex;align-items:center;justify-content:center;text-align:center;color:var(--white);font-family:"Figtree",sans-serif;font-weight:800;font-size:30px;line-height:1.15}
.footer-title{font-family:"Figtree",sans-serif;font-weight:600;font-size:17px;color:var(--white);text-transform:uppercase}
.footer-links{left:502px;top:3880px;list-style:none;color:var(--white);font-size:17px;line-height:33px}
.contact-item{left:768px;display:flex;gap:16px;color:var(--white)}
.contact-item .dot{width:52px;height:52px;border-radius:50%;background:var(--orange);display:flex;align-items:center;justify-content:center;flex:none}
.contact-item b{display:block;font-family:"Figtree",sans-serif;font-size:17px;font-weight:600}
.contact-item div{font-size:16px;line-height:21px}
.copyright{left:0;top:4158px;width:1200px;text-align:center;color:var(--white);font-family:"Figtree",sans-serif;font-weight:500;font-size:14px}
</style>
</head>
<body>
<div class="page">

  <!-- Hero -->
  <section class="hero">
    <div class="abs hero-photo" role="img" aria-label="Container port at sunset with stacked shipping containers and cranes"></div>
    <svg class="abs" style="left:0;top:500px" width="1200" height="220" viewBox="0 500 1200 220">
      <path d="M0,535 Q600,790 1200,535 L1200,720 L0,720 Z" fill="var(--orange)"/>
      <path d="M0,555 Q600,812 1200,555 L1200,720 L0,720 Z" fill="var(--white)"/>
    </svg>
    <div class="abs brand">TQ Freight<br>Global</div>
    <nav class="abs nav">
      <span class="active">Home</span>
      <span>Services<span class="caret">&#9660;</span></span>
      <span>Industries<span class="caret">&#9660;</span></span>
      <span>Request a Quote</span>
      <span>About Us</span>
      <span class="btn">Contact Us</span>
    </nav>
    <h1 class="abs heading hero-title">Delivering Strength in<br>Every Mile</h1>
    <p class="abs hero-sub">Secure and reliable transportation for all your cargo needs.</p>
    <a class="abs btn">Request a Quote</a>
  </section>

  <!-- About -->
  <section class="about">
    <div class="abs about-art" role="img" aria-label="Round emblem showing a truck over a container port collage"></div>
    <div class="abs about-copy">
      <div class="eyebrow">About Us</div>
      <h2 class="heading">Our Story</h2>
      <div class="rule"></div>
      <p>TQ Freight Global™ was born out of real-world experience in the fitness equipment industry. What started as a company shipping strength equipment, cardio machines, and training gear to gyms, schools, and commercial facilities quickly evolved into something bigger. As order volume grew and supply chains became more complex, the team developed deep expertise in coordinating freight, managing deliveries, and navigating the challenges of large-scale equipment transportation. That hands-on experience laid the foundation for what would eventually become a full-service logistics operation.</p>
      <a class="btn">Read More</a>
    </div>
  </section>

  <!-- Services -->
  <section class="services">
    <div class="abs center eyebrow" style="top:1280px">Our Services</div>
    <h2 class="abs center heading section-title" style="top:1308px">Exceeds Your Expectations</h2>
    <div class="abs center" style="top:1367px"><div class="rule"></div></div>

    <div class="abs card" style="left:149px"><h3>Flatbed<br>Transportation</h3><p>From routine shipments to oversized and heavy-haul loads, we handle freight requiring proper securement, regulatory knowledge, and consistent on-time execution.</p></div>
    <div class="abs card featured" style="left:378px"><h3>Step Deck<br>Transportation</h3><p>Our step deck trucking services support tall, heavy, and specialized freight that requires additional height clearance and flexible loading options.</p></div>
    <div class="abs card" style="left:607px"><h3>Dry Van<br>Transportation</h3><p>From consumer goods to industrial materials, our dry van services provide the space, security, and consistency you need coast to coast.</p></div>
    <div class="abs card" style="left:835px"><h3>Heavy Haul<br>Transportation</h3><p>We provide heavy haul trucking solutions for oversized, overweight, and over-dimensional freight.</p></div>

    <div class="abs card-photo" style="left:177px;background:linear-gradient(160deg,#c9b8a4,#4a3a36 60%,#1c1c1c)" role="img" aria-label="Black semi truck parked in a town"></div>
    <div class="abs card-photo" style="left:406px;background:linear-gradient(180deg,#d98a7a,#9aa7c4 50%,#555 85%)" role="img" aria-label="White semi truck on a highway at dusk"></div>
    <div class="abs card-photo" style="left:635px;background:linear-gradient(170deg,#e6e6e6,#9c9c9c 60%,#3a3a3a)" role="img" aria-label="White cargo van"></div>
    <div class="abs card-photo" style="left:863px;background:linear-gradient(170deg,#bfd0e0,#eeeeee 50%,#6a6a6a)" role="img" aria-label="Box truck at a loading dock"></div>
  </section>

  <!-- Welcome -->
  <section class="welcome">
    <div class="abs welcome-photo" role="img" aria-label="Aerial view of a busy container terminal with cranes, tinted orange"></div>
    <svg class="abs" style="left:0;top:2440px" width="1200" height="170" viewBox="0 2440 1200 170">
      <path d="M0,2447 Q600,2743 1200,2440 L1200,2610 L0,2610 Z" fill="var(--white)"/>
    </svg>
    <div class="abs welcome-copy">
      <div class="eyebrow">Welcome</div>
      <h2 class="heading">Keeping Your<br>Supply Chain Moving</h2>
      <div class="rule"></div>
      <p>We deliver a comprehensive range of open-deck and specialized transportation services—including flatbed, step deck, heavy haul, and over-dimensional freight solutions. Backed by years of experience, a trusted nationwide carrier network, and a strong safety-first culture, we provide reliable, adaptable logistics support built around the unique requirements of every load.</p>
    </div>
  </section>

  <!-- Industries -->
  <section class="industries">
    <div class="abs center eyebrow" style="top:2686px">Industries</div>
    <h2 class="abs center heading section-title" style="top:2718px">Flexible Capacity for Seasonal<br>Demand Spikes</h2>
    <div class="abs center" style="top:2822px"><div class="rule"></div></div>

    <svg class="abs dash" style="left:270px" width="82" height="30" viewBox="0 0 82 30"><path d="M2,22 Q40,-4 78,20" fill="none" stroke="#333" stroke-width="1.5" stroke-dasharray="4 4"/><path d="M72,14 L79,21 L70,23" fill="none" stroke="#333" stroke-width="1.5"/></svg>
    <svg class="abs dash" style="left:464px" width="82" height="30" viewBox="0 0 82 30"><path d="M2,20 Q40,32 78,8" fill="none" stroke="#333" stroke-width="1.5" stroke-dasharray="4 4"/><path d="M70,6 L79,8 L74,16" fill="none" stroke="#333" stroke-width="1.5"/></svg>
    <svg class="abs dash" style="left:657px" width="82" height="30" viewBox="0 0 82 30"><path d="M2,22 Q40,-4 78,20" fill="none" stroke="#333" stroke-width="1.5" stroke-dasharray="4 4"/><path d="M72,14 L79,21 L70,23" fill="none" stroke="#333" stroke-width="1.5"/></svg>
    <svg class="abs dash" style="left:850px" width="82" height="30" viewBox="0 0 82 30"><path d="M2,20 Q40,32 78,8" fill="none" stroke="#333" stroke-width="1.5" stroke-dasharray="4 4"/><path d="M70,6 L79,8 L74,16" fill="none" stroke="#333" stroke-width="1.5"/></svg>

    <div class="abs industry" style="left:138px">
      <div class="ring"><svg width="50" height="50" viewBox="0 0 50 50" fill="none" stroke="#222" stroke-width="2"><path d="M12,26 h26 M10,32 h30 M14,38 h22 v4 h-22 z M14,26 q11,-12 22,0"/><path d="M34,8 v14 M30,8 h8 v8"/></svg></div>
      <span>Food &amp; Beverage</span>
    </div>
    <div class="abs industry featured" style="left:331px">
      <div class="ring"><svg width="50" height="50" viewBox="0 0 50 50" fill="none" stroke="#fff" stroke-width="2"><rect x="8" y="9" width="34" height="24" rx="2"/><path d="M20,38 h10 M25,33 v5 M15,16 h4 l3,10 h11 l3,-7 h-15"/></svg></div>
      <span>E-Commerce &amp;<br>Retail</span>
    </div>
    <div class="abs industry" style="left:524px">
      <div class="ring"><svg width="50" height="50" viewBox="0 0 50 50" fill="none" stroke="#222" stroke-width="2"><circle cx="16" cy="14" r="5"/><path d="M16,19 v10 M16,24 l14,-8 l6,4"/><rect x="8" y="30" width="34" height="8" rx="4"/><circle cx="14" cy="34" r="1.5"/><circle cx="25" cy="34" r="1.5"/><circle cx="36" cy="34" r="1.5"/></svg></div>
      <span>Manufacturing</span>
    </div>
    <div class="abs industry" style="left:717px">
      <div class="ring"><svg width="50" height="50" viewBox="0 0 50 50" fill="none" stroke="#222" stroke-width="2"><rect x="14" y="6" width="16" height="6"/><rect x="11" y="12" width="22" height="30" rx="3"/><path d="M22,20 v12 M16,26 h12"/><rect x="32" y="32" width="12" height="7" rx="3.5"/></svg></div>
      <span>Pharma &amp; Healthcare</span>
    </div>
    <div class="abs industry" style="left:910px">
      <div class="ring"><svg width="50" height="50" viewBox="0 0 50 50" fill="none" stroke="#222" stroke-width="2"><circle cx="25" cy="17" r="9"/><circle cx="25" cy="17" r="4"/><path d="M8,34 l8,-6 l9,6 l9,-6 l8,6 M14,40 h22"/></svg></div>
      <span>Government<br>Secured Freight</span>
    </div>
  </section>

  <!-- Footer background -->
  <svg class="abs" style="left:0;top:3630px" width="1200" height="589" viewBox="0 3630 1200 589">
    <path d="M0,3650 Q600,3540 1200,3650 L1200,3690 Q600,3580 0,3690 Z" fill="var(--orange)"/>
    <path d="M0,3690 Q600,3580 1200,3690 L1200,4219 L0,4219 Z" fill="var(--black)"/>
  </svg>

  <!-- Contact -->
  <section class="contact">
    <div class="abs contact-card"></div>
    <div class="abs center eyebrow" style="top:3172px">Contact Us</div>
    <h2 class="abs center heading section-title" style="top:3212px">Let's Move Your<br>Business Forward</h2>
    <div class="abs field" style="left:239px;top:3335px;width:350px;height:56px">First Name</div>
    <div class="abs field" style="left:609px;top:3335px;width:352px;height:56px">Last Name</div>
    <div class="abs field" style="left:239px;top:3403px;width:350px;height:56px">Phone Number</div>
    <div class="abs field" style="left:609px;top:3403px;width:352px;height:56px">Email</div>
    <div class="abs field" style="left:239px;top:3472px;width:722px;height:126px">Message</div>
    <a class="abs btn">Send Now</a>
  </section>

  <!-- Footer -->
  <footer>
    <div class="abs footer-brand">TQ Freight<br>Global</div>
    <div class="abs footer-title" style="left:494px;top:3828px">Quick Links</div>
    <ul class="abs footer-links">
      <li>Home</li><li>Services</li><li>Industries</li><li>Request a Quote</li><li>About Us</li><li>Contact Us</li>
    </ul>
    <div class="abs footer-title" style="left:768px;top:3828px">Get in Touch</div>
    <div class="abs contact-item" style="top:3868px">
      <span class="dot"><svg width="22" height="22" viewBox="0 0 24 24"><path d="M12,2 a7,7 0 0 1 7,7 c0,5 -7,13 -7,13 s-7,-8 -7,-13 a7,7 0 0 1 7,-7z" fill="#fff"/><circle cx="12" cy="9" r="2.6" fill="var(--orange)"/></svg></span>
      <div><b>Location</b>Sed ut perspiciatis unde<br>omnis iste natus</div>
    </div>
    <div class="abs contact-item" style="top:3962px">
      <span class="dot"><svg width="22" height="22" viewBox="0 0 24 24"><path d="M6.6,10.8 a15,15 0 0 0 6.6,6.6 l2.2,-2.2 a1,1 0 0 1 1,-.25 a11,11 0 0 0 3.6,.6 a1,1 0 0 1 1,1 V20 a1,1 0 0 1 -1,1 A17,17 0 0 1 3,4 a1,1 0 0 1 1,-1 h3.5 a1,1 0 0 1 1,1 a11,11 0 0 0 .6,3.6 a1,1 0 0 1 -.25,1z" fill="#fff"/></svg></span>
      <div><b>Call Us</b>+1 555-014-2290</div>
    </div>
    <div class="abs contact-item" style="top:4042px">
      <span class="dot"><svg width="22" height="22" viewBox="0 0 24 24" fill="none" stroke="#fff" stroke-width="2"><rect x="3" y="5" width="18" height="14" rx="2"/><path d="M3,7 l9,6 l9,-6"/></svg></span>
      <div><b>Email</b>info@tqfreightglobal.com</div>
    </div>
    <div class="abs" style="left:149px;top:4134px;width:900px;height:1px;background:#2c2c2c"></div>
    <p class="abs copyright">© 2026. TQ Freight Global. All rights reserved.</p>
  </footer>

</div>
</body>
</html>
```